Business Card Design Project

We need a business card for a new technology services company. We develop software and implement software packages for our business customers and although we will begin with just one or two service offerings, our service offerings will expand over time. Our name comes from the an author, KL Barrow, and his "idea" was that opportunity should be based on ability and achievement, not on social status.

We would like to see a design that is standard in its size and shape, but stands apart in its dramatic color contrasts. The card should not use too many colors - the colors used in the background should highlight the brilliant blues of the logo (see attachment) to dramatic effect. The background should not be white.

If necessary, you can change the color of the words "KL Barrow", but not the word "Idea".

Card size should be U.S. standard 2 inches by 3.5 inches and provide for 1/8 inch bleed area on each side.

We need a design for both sides of the business card, one side communicating the company logo and contact information, the other side being purely graphical, incorporating the logo but no other information.

Contact Information Required:
Kate Brook
KateBrook@klbarrowvista.com
614-387-2259

Target Market(s)

Business executives

Industry/Entity Type

Software

Requirements
Must have
• It must have the full company logo on one side, and at least the graphic element of the logo on the other. Either that or the full logo on both.
Nice to have
• It would be nice to have a design that could work without needing two different textures. For example, it would be nice if the entire card could be shiny, not just parts of the card.

It would also be nice if texture is something we could add later.
Should not have
• The card should not use the color green.

```html
<!DOCTYPE html>
<html lang="en">
<head>
<meta charset="utf-8">
<title>Barrow Vista — Business Card</title>
<link rel="stylesheet" href="https://fonts.googleapis.com/css2?family=Arimo:wght@400;700&display=swap">
<style>
  :root {
    --stage: #d9d6d2;
    --card-top: #1c1c1c;
    --card-bottom: #060606;
    --brand-blue: #12a3e3;
    --brand-blue-deep: #0a8fcc;
    --rule-grey: #9a9a9a;
    --ink-light: #f2f2f2;
    --faint-blue: rgba(18, 163, 227, 0.28);
  }
  * { box-sizing: border-box; margin: 0; padding: 0; }
  html, body {
    width: 1200px; height: 750px; overflow: hidden;
    background: var(--stage);
    font-family: "Arimo", Arial, sans-serif;
  }
  .stage {
    position: relative; width: 1200px; height: 750px;
    display: flex; align-items: center; justify-content: center; gap: 40px;
  }
  .card {
    position: relative; width: 540px; height: 309px; overflow: hidden;
    background:
      repeating-linear-gradient(90deg, rgba(255,255,255,0.018) 0 2px, transparent 2px 5px),
      radial-gradient(ellipse at 45% 35%, var(--card-top), var(--card-bottom) 75%);
    box-shadow: 0 8px 24px rgba(0,0,0,0.35);
  }

  /* Front side */
  .front .brand {
    position: absolute; left: 28px; top: 136px;
    display: flex; align-items: center; gap: 10px;
  }
  .brand-dot {
    width: 16px; height: 16px; border-radius: 50%;
    background: var(--brand-blue);
  }
  .brand-name {
    font-size: 28px; font-weight: 400; letter-spacing: -0.3px;
    color: var(--brand-blue); white-space: nowrap;
  }
  .front .divider {
    position: absolute; left: 262px; top: 52px; width: 2px; height: 128px;
    background: linear-gradient(180deg, transparent, #d8d8d8 50%, transparent);
  }
  .contact {
    position: absolute; left: 284px; top: 62px;
  }
  .contact-name {
    font-size: 20px; font-weight: 700; letter-spacing: 0.5px;
    color: var(--brand-blue); text-transform: uppercase;
    margin-bottom: 24px;
  }
  .contact-line {
    display: flex; align-items: center; gap: 8px;
    font-size: 13px; color: var(--ink-light);
    margin-bottom: 12px; white-space: nowrap;
  }
  .contact-line svg { width: 12px; height: 12px; flex: none; }
  .front .rule {
    position: absolute; left: 0; right: 0; bottom: 38px; height: 3px;
    background: var(--rule-grey);
  }
  .front .band {
    position: absolute; left: 0; right: 0; bottom: 0; height: 32px;
    background: linear-gradient(180deg, var(--brand-blue), var(--brand-blue-deep));
  }

  /* Back side */
  .back .mark-circle {
    position: absolute; left: 170px; top: 40px;
    width: 230px; height: 230px; border-radius: 50%;
    background: var(--faint-blue);
  }
  .back .brand-name.large {
    position: absolute; left: 70px; top: 118px;
    font-size: 66px; letter-spacing: -1px;
  }
</style>
</head>
<body>
<main class="stage">
  <section class="card front" aria-label="Card front">
    <div class="brand">
      <span class="brand-name">Barrow Vista</span>
      <span class="brand-dot"></span>
    </div>
    <div class="divider"></div>
    <div class="contact">
      <p class="contact-name">Kate Brook</p>
      <p class="contact-line">
        <svg viewBox="0 0 12 12" aria-hidden="true"><path d="M3 1l2 2.5-1.2 1.2c.6 1.4 1.6 2.4 3 3L8 6.5 10.5 8.5 9.5 10.5C5 10.5 1.5 7 1.5 2.5z" fill="var(--brand-blue)"/></svg>
        614-387-2259
      </p>
      <p class="contact-line">
        <svg viewBox="0 0 12 12" aria-hidden="true"><rect x="1" y="3" width="10" height="7" fill="var(--brand-blue)"/><path d="M1 3l5 4 5-4" stroke="#0b0b0b" stroke-width="1" fill="none"/></svg>
        KateBrook@klbarrowvista.com
      </p>
    </div>
    <div class="rule"></div>
    <div class="band"></div>
  </section>

  <section class="card back" aria-label="Card back">
    <div class="mark-circle"></div>
    <span class="brand-name large">Barrow Vista</span>
  </section>
</main>
</body>
</html>
```